Nano particle enhanced sprays for Chinese market

Our company is soon launching a range of nano particle-infused sprays for Chinese market. We have several different products, the main feature we want to emphasize is the nanotechnology inside, market the product as a high tech, future tech for everyday use. We also want to subtly include the fact that this is an European technology (our company is in China, however I as well as the technology are both from the EU).

The design should be minimalist, and have a sort of a “nanovibe” to it.

We have nine different products (see below), but it does not necessarily mean that we need nine different designs. Our idea is to have one general design, only change the product name, colors and a background/icon – you guys are the professionals, we will leave that to you.

Our spray can will have various sizes, you can use a 350ml with radius of 4.5 cm and height of 15 cm (the bottle print area is 14.13x15).

I have attached our previous attempt at designing the bottle, it can give you an idea – do not take any inspiration from it, I have attached another 8 pictures of a designs we actually like (labeled inspiration1….8.jpg)

I am not sure if it is of any relevance to you, but we already committed to produce 100.000 units. It should hit the shelves in early August.

I also noticed that there are some people that would close the listing just days before end so we decided to make this a guaranteed payment.

Good luck and may the force be with you!

Target Market(s)

Retail supermarket, gas stations, car supply shops.

Industry/Entity Type

It Company

Requirements
Must have
• On the front side, we want to have our company logo (can be small, see attached - change the colors and text position as you like), the product name (both English and Chinese) - see attached word file for list of product names and brief description.

The Chinese name is the most important, English brand should be secondary.

Back side is for the following information:

1: Product description
2. Usage instructions
3. Safety instructions
4. Contents
5. Legal info
5. Recycle icons, barcode

The information should be in Chinese and English. Text can be very small.
Nice to have
• This really depends on your professional judgement, it is not a request, only an option.

A one sentence product description in Chinese only. You can use the following text for as a sample – 欧洲纳米技术的热表面的瞬间冻结

and/or

Three or four highlights in either only Chinese or both English and Chinese. You can use the following as a sample:

1. 欧洲纳米技术/European Nanotechnology
2. 瞬间冻结/Instant Freeze
3. 环保/Environmentally Friendly

The product is (at this stage) targeted on Chinese market only. The only purpose of adding the English text is to enhance the feeling of a high quality product.

```html
<!DOCTYPE html>
<html lang="zh">
<head>
<meta charset="utf-8">
<title>CHILLMIST 食品速冻喷雾 – Label</title>
<link rel="stylesheet" href="https://fonts.googleapis.com/css2?family=Roboto+Condensed:wght@400;700&family=Noto+Serif+SC:wght@400;700&display=swap">
<style>
  :root {
    --page-bg: #f1f1f1;
    --label-light: #cfe9e6;
    --label-mid: #9fd3cd;
    --label-deep: #6fbab4;
    --ice: #4f9ea0;
    --ink: #1c5671;
    --ink-dark: #123e52;
    --text: #1f2f38;
    --badge-bg: #123040;
    --badge-text: #ffffff;
  }
  html, body {
    margin: 0;
    width: 1035px;
    height: 1200px;
    overflow: hidden;
    background: var(--page-bg);
  }
  .canvas {
    position: relative;
    width: 1035px;
    height: 1200px;
  }
  .label {
    position: absolute;
    left: 368px;
    top: 330px;
    width: 300px;
    height: 765px;
    overflow: hidden;
    background: linear-gradient(160deg, var(--label-light) 0%, var(--label-mid) 50%, var(--label-deep) 100%);
    text-align: center;
    color: var(--text);
  }
  .label-artwork {
    position: absolute;
    inset: 0;
  }
  .ice-band {
    position: absolute;
    left: 0;
    right: 0;
    bottom: 0;
    height: 165px;
    background: linear-gradient(180deg, rgba(79,158,160,0) 0%, var(--ice) 45%, #3e8d90 100%);
  }
  .brand {
    position: absolute;
    top: 108px;
    left: 0;
    right: 0;
    display: flex;
    flex-direction: column;
    align-items: center;
    gap: 8px;
  }
  .brand-mark {
    width: 44px;
    height: 44px;
    background: var(--ink);
  }
  .brand-name {
    font-family: "Roboto Condensed", sans-serif;
    font-weight: 700;
    font-size: 21px;
    letter-spacing: 1px;
    color: var(--ink);
  }
  .product-en {
    position: absolute;
    top: 266px;
    left: 0;
    right: 0;
    margin: 0;
    font-family: "Roboto Condensed", sans-serif;
    font-weight: 700;
    font-size: 42px;
    line-height: 1;
    color: var(--ink);
  }
  .product-cn {
    position: absolute;
    top: 314px;
    left: 0;
    right: 0;
    font-family: "Noto Serif SC", serif;
    font-size: 31px;
    line-height: 1.2;
    letter-spacing: 3px;
    color: var(--ink-dark);
  }
  .tagline {
    position: absolute;
    top: 380px;
    left: 0;
    right: 0;
    margin: 0;
    font-family: "Noto Serif SC", serif;
    font-weight: 700;
    font-size: 19px;
    line-height: 29px;
    color: var(--text);
  }
  .highlights {
    position: absolute;
    top: 485px;
    left: 0;
    right: 0;
    margin: 0;
    padding: 0;
    list-style: none;
    font-family: "Noto Serif SC", serif;
    font-size: 12px;
    line-height: 17px;
    color: var(--text);
  }
  .volume {
    position: absolute;
    bottom: 10px;
    left: 50%;
    transform: translateX(-50%);
    padding: 3px 8px;
    border-radius: 5px;
    background: var(--badge-bg);
    color: var(--badge-text);
    font-family: "Noto Serif SC", serif;
    font-weight: 700;
    font-size: 14px;
  }
</style>
</head>
<body>
<div class="canvas">
  <section class="label">
    <div class="label-artwork" role="img" aria-label="Faceted crystal background with nano bubbles"></div>
    <div class="ice-band" role="img" aria-label="Crushed ice cubes"></div>

    <div class="brand">
      <div class="brand-mark"></div>
      <div class="brand-name">VELORIN</div>
    </div>

    <h1 class="product-en">CHILLMIST</h1>
    <div class="product-cn">食品速冻喷雾</div>

    <p class="tagline">欧洲纳米技术的热表面的<br>瞬间冻结</p>

    <ul class="highlights">
      <li>欧洲纳米技术/European Nanotechnology</li>
      <li>瞬间冻结/Instant Freeze</li>
      <li>环保/Environmentally Friendly</li>
    </ul>

    <div class="volume">350ml</div>
  </section>
</div>
</body>
</html>
```